Vantoq Business Card Project showing the logo and a marbo image on the rear

Design a whacky but professional business card, the logo is for the front and the Marbo image is for the rear. Happy to consider other open source Marbo Images if the designer wants to select one from the web. Vantoq is a competitor to OMB.com.au and Pellory.com.au and is based around every property in Australia

Target Market(s)

Business

Contact Information for Business Card

Name, Title, Email, Web, Phone Number

Font styles to use
Other font styles liked:
• avenir

Requirements
Must have
• Image on Back logo on front
Nice to have
• Happy to consider other images on rear, preftably Colin Marbo. Image supplied I own, we can use open source other Marbo Images

```html
<!DOCTYPE html>
<html lang="en">
<head>
<meta charset="utf-8">
<title>Vantoq Business Card</title>
<link rel="stylesheet" href="https://fonts.googleapis.com/css2?family=Nunito+Sans:wght@700;800&family=Roboto:wght@400;500&display=swap">
<style>
  :root {
    --backdrop: #2b2b2b;
    --card: #ececec;
    --orange: #e8870f;
    --ink: #111111;
    --night: #3a3b3d;
  }
  * { margin: 0; padding: 0; box-sizing: border-box; }
  html, body { width: 1200px; height: 1138px; overflow: hidden; }
  body { background: var(--backdrop); position: relative; font-family: "Roboto", Arial, sans-serif; color: var(--ink); }

  .card { position: absolute; border-radius: 14px; overflow: hidden; }

  .card-rear { left: 274px; top: 185px; width: 624px; height: 377px; }
  .artwork {
    width: 100%; height: 100%;
    background: linear-gradient(90deg, var(--orange) 0%, var(--orange) 49%, var(--night) 51%, var(--night) 100%);
  }
  .artwork::after {
    content: ""; position: absolute; left: 0; right: 0; bottom: 0; height: 66%;
    background: linear-gradient(180deg, rgba(220,90,160,0.85), rgba(120,190,200,0.9) 72%, rgba(110,180,70,0.95));
  }

  .card-front { left: 276px; top: 608px; width: 618px; height: 374px; background: var(--card); }
  .wave { position: absolute; left: 0; top: 0; width: 618px; height: 140px; }

  .tagline {
    position: absolute; right: 36px; top: 24px; text-align: right;
    font-size: 15.5px; line-height: 24px; color: var(--ink);
  }

  .brand-mark { position: absolute; left: 30px; top: 98px; width: 92px; height: 92px; background: var(--orange); border-radius: 4px; }
  .brand-name {
    position: absolute; left: 146px; top: 117px;
    font-family: "Nunito Sans", Arial, sans-serif; font-weight: 800;
    font-size: 86px; line-height: 1; color: var(--ink); letter-spacing: 0.5px;
  }

  .contact { position: absolute; left: 30px; top: 247px; list-style: none; font-size: 16.5px; }
  .contact li { display: flex; align-items: center; height: 24px; }
  .contact svg { width: 14px; height: 14px; margin-right: 18px; flex: none; }
  .contact .accent { color: var(--orange); }
  .contact-address { position: absolute; left: 30px; top: 322px; font-size: 16.5px; line-height: 24px; }

  .person { position: absolute; right: 34px; top: 272px; text-align: right; }
  .person-name { font-family: "Nunito Sans", Arial, sans-serif; font-weight: 700; font-size: 25px; color: var(--orange); line-height: 30px; }
  .person-title { font-size: 16px; line-height: 24px; }
</style>
</head>
<body>

<section class="card card-rear">
  <div class="artwork" role="img" aria-label="Colourful cartoon city skyline artwork: a daytime orange sky on the left, a night sky on the right, bright buildings and a train along the bottom"></div>
</section>

<section class="card card-front">
  <svg class="wave" viewBox="0 0 618 140" aria-hidden="true">
    <path d="M0 0 H618 V104 C560 118 500 96 430 72 C300 24 150 2 0 44 Z" fill="var(--orange)"/>
    <path d="M0 60 C150 10 300 32 430 86 C500 116 560 128 618 114" fill="none" stroke="var(--ink)" stroke-width="7"/>
  </svg>

  <p class="tagline">Buying, Selling<br>and Research</p>

  <span class="brand-mark"></span>
  <span class="brand-name">Vantoq</span>

  <ul class="contact">
    <li>
      <svg viewBox="0 0 16 16"><circle cx="8" cy="8" r="6.5" fill="none" stroke="var(--orange)" stroke-width="1.5"/><path d="M5.5 4.5 L7 6 L6.2 7 C6.8 8.3 7.7 9.2 9 9.8 L10 9 L11.5 10.5 L10.5 11.6 C7.5 11 5 8.5 4.4 5.5 Z" fill="var(--orange)"/></svg>
      (02) 4817 2690
    </li>
    <li>
      <svg viewBox="0 0 16 16"><rect x="1" y="3" width="14" height="10" fill="var(--orange)"/><path d="M1 3 L8 9 L15 3" fill="none" stroke="var(--card)" stroke-width="1.4"/></svg>
      talbrick@vantoq.com
    </li>
    <li>
      <svg viewBox="0 0 16 16"><circle cx="8" cy="8" r="6.5" fill="var(--orange)"/><path d="M1.5 8 H14.5 M8 1.5 V14.5 M8 1.5 C4.5 5 4.5 11 8 14.5 M8 1.5 C11.5 5 11.5 11 8 14.5" fill="none" stroke="var(--card)" stroke-width="0.9"/></svg>
      www.<span class="accent">vantoq</span>.com
    </li>
  </ul>
  <p class="contact-address">Level 7, 48 Harlow Street, Sydney 2000, AU</p>

  <div class="person">
    <p class="person-name">Owen Talbrick</p>
    <p class="person-title">Founder &amp; CEO</p>
  </div>
</section>

</body>
</html>
```